Brightbay Orthodontics business card design

Need a business card design that reflects our re-branding (orthodontic office - braces) and a new partnership with a pediatric dental office. We would like to include "for adults and children" on the card as well so adults know they are welcome to get their braces here as well. Office design is modern and would like business card to reflect a modern type look. Here's the text we would like to be included on the card:

Darren Wolcott, DDS, MSD
5214 West Linden Avenue, Suite 204
Mansfield, TX 76991
555-418-2637
www.brightbayortho.example
info@brightbayortho.example

Can we add the following to the existing designs? Darren Wolcott, DDS, MSD 5214 West Linden Avenue, Suite 204 Mansfield, TX 76991 555-418-2637

Does anyone have any more vertical designs available? Thanks!

Dental

```html
<!DOCTYPE html>
<html lang="en">
<head>
<meta charset="utf-8">
<title>Brightbay Orthodontics business card</title>
<link href="https://fonts.googleapis.com/css2?family=Open+Sans:wght@400;600;700&display=swap" rel="stylesheet">
<style>
  :root {
    --backdrop: #e4e5e7;
    --card: #ffffff;
    --ink-grey: #6d6e71;
    --text-grey: #5f6064;
    --name-blue: #7b9cc8;
    --band-blue: #2d5ea6;
    --band-green: #8cc63f;
    --tooth-light: #f4f5f7;
    --tooth-shade: #d9dce1;
  }
  * { margin: 0; padding: 0; box-sizing: border-box; }
  html, body { width: 1200px; height: 753px; overflow: hidden; }
  body {
    background: var(--backdrop);
    font-family: "Open Sans", Arial, sans-serif;
    position: relative;
  }
  .card {
    position: absolute;
    top: 88px;
    width: 330px;
    height: 578px;
    background: var(--card);
    box-shadow: 0 6px 18px rgba(0,0,0,0.12);
    overflow: hidden;
  }
  .card--front { left: 190px; }
  .card--back { left: 680px; }

  /* Front */
  .front-brand {
    position: absolute;
    left: 50%;
    top: 50%;
    transform: translate(-50%, -50%) rotate(-90deg);
    white-space: nowrap;
    text-align: center;
  }
  .front-brand__name {
    font-weight: 700;
    font-size: 38px;
    line-height: 46px;
    color: var(--ink-grey);
    letter-spacing: 0.5px;
  }
  .front-brand__tagline {
    font-size: 15px;
    font-weight: 400;
    color: var(--text-grey);
    margin-top: 4px;
    letter-spacing: 0.5px;
  }

  /* Back */
  .back-brand {
    position: absolute;
    top: 36px;
    left: 0;
    width: 100%;
    text-align: center;
  }
  .back-brand__name {
    font-weight: 700;
    font-size: 20px;
    line-height: 26px;
    color: var(--ink-grey);
  }
  .back-brand__tagline {
    font-size: 11px;
    color: var(--text-grey);
    margin-top: 4px;
  }
  .chevron { position: absolute; left: 0; top: 0; }
  .tooth-art {
    position: absolute;
    right: -30px;
    top: 215px;
    width: 130px;
    height: 270px;
    border-radius: 60px 60px 40px 40px;
    background: linear-gradient(160deg, var(--tooth-light), var(--tooth-shade));
  }
  .doctor {
    position: absolute;
    top: 232px;
    left: 0;
    width: 100%;
    text-align: center;
  }
  .doctor__name { font-size: 19px; color: var(--name-blue); font-weight: 400; }
  .doctor__title { font-size: 11px; color: var(--text-grey); margin-top: 3px; }
  .address {
    position: absolute;
    left: 22px;
    top: 390px;
    font-size: 11.5px;
    line-height: 17px;
    color: var(--text-grey);
  }
  .contacts {
    position: absolute;
    left: 22px;
    top: 440px;
    list-style: none;
    font-size: 12px;
    line-height: 22px;
    color: var(--text-grey);
  }
  .contacts li { display: flex; align-items: center; gap: 9px; }
  .contacts svg { width: 11px; height: 11px; fill: var(--band-blue); }
  .bands { position: absolute; left: 0; bottom: 0; }
</style>
</head>
<body>
  <section class="card card--front" aria-label="Card front">
    <div class="front-brand">
      <div class="front-brand__name">Brightbay Orthodontics</div>
      <div class="front-brand__tagline">for adults and children</div>
    </div>
  </section>

  <section class="card card--back" aria-label="Card back">
    <div class="back-brand">
      <div class="back-brand__name">Brightbay Orthodontics</div>
      <div class="back-brand__tagline">for adults and children</div>
    </div>
    <svg class="chevron" width="330" height="240" viewBox="0 0 330 240">
      <polyline points="0,178 170,186 330,55" fill="none" stroke="var(--band-green)" stroke-width="2"/>
    </svg>

    <div class="tooth-art" role="img" aria-label="Large soft white tooth illustration"></div>

    <div class="doctor">
      <div class="doctor__name">Darren Wolcott</div>
      <div class="doctor__title">DDS, MSD</div>
    </div>

    <div class="address">
      5214 West Linden Avenue, Suite 204<br>
      Mansfield, TX 76991
    </div>

    <ul class="contacts">
      <li>
        <svg viewBox="0 0 16 16"><path d="M3 1h3l1.5 4-2 1.5a9 9 0 0 0 4 4L11 8.5l4 1.5v3a2 2 0 0 1-2 2A12 12 0 0 1 1 3a2 2 0 0 1 2-2z"/></svg>
        555-418-2637
      </li>
      <li>
        <svg viewBox="0 0 16 16"><circle cx="8" cy="8" r="7" fill="none" stroke="var(--band-blue)" stroke-width="1.5"/><path d="M1 8h14M8 1c-3 3.5-3 10.5 0 14M8 1c3 3.5 3 10.5 0 14" fill="none" stroke="var(--band-blue)" stroke-width="1.2"/></svg>
        www.brightbayortho.example
      </li>
      <li>
        <svg viewBox="0 0 16 16"><rect x="1" y="3" width="14" height="10" rx="1"/><path d="M1 4l7 5 7-5" fill="none" stroke="#fff" stroke-width="1.2"/></svg>
        info@brightbayortho.example
      </li>
    </ul>

    <svg class="bands" width="330" height="60" viewBox="0 0 330 60">
      <polygon points="190,22 330,10 330,20 200,30" fill="var(--band-green)"/>
      <polygon points="0,40 200,30 330,20 330,60 0,60" fill="var(--band-blue)"/>
    </svg>
  </section>
</body>
</html>
```